New start-up company catalog!

Heat transfer printing company. We are set to launch later this month and need a stand out catalog to wow our customers. We are a printing/manufacturing heat transfer company geared towards apparel and promotional items.

```html
<!DOCTYPE html>
<html lang="en">
<head>
<meta charset="utf-8">
<title>Heat Transfers Catalog Spread</title>
<link href="https://fonts.googleapis.com/css2?family=Montserrat:wght@500;600;700;800&display=swap" rel="stylesheet">
<style>
:root{
  --stage:#58585a;
  --paper:#ffffff;
  --teal:#3cc3c6;
  --purple-dark:#2e2a78;
  --purple:#5b3aa8;
  --purple-light:#7a44c0;
  --orange:#f7a823;
  --pink:#e0168a;
  --navy-ink:#1f2a66;
  --row:#dcf1f1;
  --row-alt:#c9e9ea;
  --font:"Montserrat",sans-serif;
}
*{margin:0;padding:0;box-sizing:border-box}
html,body{width:1200px;height:936px;overflow:hidden;background:var(--stage);font-family:var(--font)}
.page{position:absolute;width:523px;height:406px;background:var(--paper);overflow:hidden}
.p1{left:51px;top:35px}.p2{left:620px;top:35px}
.p3{left:51px;top:488px}.p4{left:620px;top:488px}
.corner-tab{position:absolute;bottom:0;width:13px;height:11px;background:var(--pink)}
.cover .corner-tab{left:5px}.pricing .corner-tab{right:5px}

/* cover page */
.cover{background:var(--teal)}
.cover .wedge{position:absolute;inset:0}
.apparel-photo{position:absolute;left:4px;top:18px;width:420px;height:290px;border-radius:40px 40px 0 0;
  background:linear-gradient(100deg,#6a35b5 0%,#1a1a22 32%,#7a36c4 52%,#1d5a34 72%,#241a55 100%);opacity:.92}
.product-title{position:absolute;right:16px;top:22px;text-align:right;font-weight:800;font-size:19.5px;line-height:18.5px;letter-spacing:.5px}
.product-title span{display:inline-block;background:var(--purple);color:var(--orange);padding:0 2px}
.product-title .last{color:var(--teal)}
.fabric-band{position:absolute;left:13px;top:292px;width:510px;height:82px;
  background:linear-gradient(90deg,var(--purple-dark) 0%,var(--purple) 70%,var(--purple-light) 100%)}
.fabric-band h2{position:absolute;left:10px;top:8px;color:#fff;font-weight:600;font-size:21px;line-height:23px;letter-spacing:.6px}
.fabric-band p{position:absolute;left:278px;top:7px;width:218px;color:var(--orange);font-weight:600;font-size:7.4px;line-height:9.2px}
.p3 .fabric-band{top:294px;height:80px}
.p3 .fabric-band h2{top:6px;line-height:22.5px}
.color-tag{position:absolute;right:0;background:var(--teal);color:#fff;font-weight:600;padding-left:10px;display:flex;align-items:center}
.p1 .color-tag{top:369px;width:190px;height:18px;font-size:8.2px}
.p3 .color-tag{top:370px;width:113px;height:18px;font-size:11px}

/* pricing page */
.section-bar{position:absolute;left:0;width:510px;background:linear-gradient(90deg,var(--purple) 0%,var(--purple-dark) 100%);color:#fff}
.title-bar{top:23px;height:22px;font-size:16px;font-weight:600;padding-left:24px;line-height:22px;letter-spacing:.3px}
.colors-bar{top:278px;height:21px;font-size:7px;font-weight:600;padding:2px 0 0 24px;line-height:8px}
.price-table{position:absolute;border-collapse:collapse;font-size:5.6px;font-weight:600;color:var(--navy-ink)}
.price-table th{background:var(--purple-dark);color:#fff;font-weight:600;padding:0 3px;height:7.6px;text-align:left;white-space:nowrap}
.price-table td{height:7.6px;padding:0 3px;white-space:nowrap;text-align:right}
.price-table td:first-child{text-align:center}
.price-table tr:nth-child(odd) td{background:var(--row)}
.price-table tr:nth-child(even) td{background:var(--row-alt)}
.p2 .t1{left:90px;top:77px;width:168px}.p2 .t2{left:264px;top:77px;width:166px}
.p2 .t3{left:90px;top:167px;width:168px}.p2 .t4{left:264px;top:167px;width:166px}
.p4 .t1{left:116px;top:70px;width:134px}.p4 .t2{left:266px;top:70px;width:141px}
.p4 .t3{left:116px;top:168px;width:134px}.p4 .t4{left:266px;top:168px;width:141px}
.swatches{position:absolute;left:18px;top:306px;width:490px;display:grid;grid-template-columns:repeat(11,38px);column-gap:6.4px;row-gap:7px}
.swatch{height:39px;color:#fff;font-size:5.6px;font-weight:600;line-height:6.3px;display:flex;flex-direction:column;justify-content:flex-end;padding:0 0 2px 2px}
.swatch.white{border:1px solid #bbb;color:#333}
</style>
</head>
<body>

<section class="page cover p1">
  <svg class="wedge" width="523" height="406"><polygon points="0,250 523,95 523,406 0,406" fill="#fff"/></svg>
  <div class="apparel-photo" role="img" aria-label="Group of polyester hoodies, polo, long sleeve tee and tank top with printed school and club graphics"></div>
  <div class="product-title"><span>VARSITY</span><br><span>FORMULA</span><br><span>HEAT</span><br><span class="last">TRANSFERS</span></div>
  <div class="fabric-band">
    <h2>FOR 100% POLYESTER<br>AND 50/50 COTTON<br>POLY BLENDS</h2>
    <p>Our most versatile product offering yet! Decorate the most popular fabric types including 100% Polyester, Cotton Blends or 100% cotton. We provide (4) different sheet sizes options which offers you the ability to "gang" as many images on the sheet for one low price! Application is quick and easy! Hot peel them in only 7 seconds!</p>
  </div>
  <div class="color-tag">1, 2, 3 Color or Unlimited color options</div>
  <div class="corner-tab"></div>
</section>

<section class="page pricing p2">
  <div class="section-bar title-bar">Sizing &amp; Pricing</div>
  <table class="price-table t1"><tr><th>Varsity 4x6</th><th>1 color</th><th>2 color</th><th>3 color</th><th>Process</th></tr>
    <tr><td>8</td><td>$ 4.80</td><td>$ 8.75</td><td>$ 12.58</td><td>$ 6.13</td></tr>
    <tr><td>16</td><td>$ 2.43</td><td>$ 4.55</td><td>$ 6.38</td><td>$ 4.78</td></tr>
    <tr><td>24</td><td>$ 1.62</td><td>$ 3.08</td><td>$ 4.28</td><td>$ 3.73</td></tr>
    <tr><td>32</td><td>$ 1.30</td><td>$ 2.50</td><td>$ 3.28</td><td>$ 3.03</td></tr>
    <tr><td>48</td><td>$ 1.12</td><td>$ 2.05</td><td>$ 3.03</td><td>$ 2.63</td></tr>
    <tr><td>72</td><td>$ 0.90</td><td>$ 1.53</td><td>$ 2.38</td><td>$ 2.23</td></tr>
    <tr><td>96</td><td>$ 0.70</td><td>$ 1.19</td><td>$ 1.78</td><td>$ 1.68</td></tr>
    <tr><td>144</td><td>$ 0.49</td><td>$ 1.15</td><td>$ 1.23</td><td>$ 1.23</td></tr>
    <tr><td>288</td><td>$ 0.39</td><td>$ 0.55</td><td>$ 0.88</td><td>$ 0.83</td></tr>
    <tr><td>512</td><td>$ 0.24</td><td>$ 0.49</td><td>$ 0.63</td><td>$ 0.63</td></tr></table>
  <table class="price-table t2"><tr><th>Varsity 6x9</th><th>1 color</th><th>2 color</th><th>3 color</th><th>Process</th></tr>
    <tr><td>8</td><td>$ 6.25</td><td>$ 11.70</td><td>$ 17.25</td><td>$ 12.03</td></tr>
    <tr><td>16</td><td>$ 3.18</td><td>$ 5.95</td><td>$ 8.63</td><td>$ 6.13</td></tr>
    <tr><td>24</td><td>$ 2.19</td><td>$ 4.00</td><td>$ 5.78</td><td>$ 4.38</td></tr>
    <tr><td>32</td><td>$ 1.73</td><td>$ 3.13</td><td>$ 4.48</td><td>$ 3.38</td></tr>
    <tr><td>48</td><td>$ 1.52</td><td>$ 2.68</td><td>$ 3.93</td><td>$ 3.03</td></tr>
    <tr><td>72</td><td>$ 1.29</td><td>$ 2.23</td><td>$ 3.18</td><td>$ 2.43</td></tr>
    <tr><td>96</td><td>$ 1.09</td><td>$ 1.88</td><td>$ 2.68</td><td>$ 1.83</td></tr>
    <tr><td>144</td><td>$ 0.99</td><td>$ 1.53</td><td>$ 2.18</td><td>$ 1.63</td></tr>
    <tr><td>288</td><td>$ 0.68</td><td>$ 1.08</td><td>$ 1.53</td><td>$ 1.53</td></tr>
    <tr><td>512</td><td>$ 0.49</td><td>$ 0.83</td><td>$ 1.23</td><td>$ 1.18</td></tr></table>
  <table class="price-table t3"><tr><th>Varsity 9x12.75</th><th>1 color</th><th>2 color</th><th>3 color</th><th>Process</th></tr>
    <tr><td>8</td><td>$ 6.85</td><td>$ 13.10</td><td>$ 19.13</td><td>$ 19.48</td></tr>
    <tr><td>16</td><td>$ 3.65</td><td>$ 6.68</td><td>$ 9.58</td><td>$ 10.23</td></tr>
    <tr><td>24</td><td>$ 2.48</td><td>$ 4.47</td><td>$ 6.43</td><td>$ 6.88</td></tr>
    <tr><td>32</td><td>$ 2.18</td><td>$ 3.63</td><td>$ 5.13</td><td>$ 5.43</td></tr>
    <tr><td>48</td><td>$ 1.79</td><td>$ 3.08</td><td>$ 4.33</td><td>$ 3.93</td></tr>
    <tr><td>72</td><td>$ 1.53</td><td>$ 2.48</td><td>$ 3.58</td><td>$ 3.18</td></tr>
    <tr><td>96</td><td>$ 1.28</td><td>$ 2.18</td><td>$ 3.13</td><td>$ 2.63</td></tr>
    <tr><td>144</td><td>$ 1.14</td><td>$ 1.98</td><td>$ 2.58</td><td>$ 2.18</td></tr>
    <tr><td>288</td><td>$ 0.84</td><td>$ 1.38</td><td>$ 1.88</td><td>$ 1.83</td></tr>
    <tr><td>512</td><td>$ 0.59</td><td>$ 1.03</td><td>$ 1.48</td><td>$ 1.33</td></tr></table>
  <table class="price-table t4"><tr><th>Varsity 19x12.75</th><th>1 color</th><th>2 color</th><th>3 color</th><th>Process</th></tr>
    <tr><td>8</td><td>$ 8.30</td><td>$ 16.10</td><td>$ 23.98</td><td>n/a</td></tr>
    <tr><td>16</td><td>$ 4.90</td><td>$ 8.93</td><td>$ 12.03</td><td>n/a</td></tr>
    <tr><td>24</td><td>$ 3.42</td><td>$ 5.98</td><td>$ 8.73</td><td>$ 11.68</td></tr>
    <tr><td>32</td><td>$ 2.88</td><td>$ 5.13</td><td>$ 7.33</td><td>$ 8.93</td></tr>
    <tr><td>48</td><td>$ 2.18</td><td>$ 3.73</td><td>$ 5.38</td><td>$ 7.38</td></tr>
    <tr><td>72</td><td>$ 1.89</td><td>$ 3.23</td><td>$ 4.38</td><td>$ 5.28</td></tr>
    <tr><td>96</td><td>$ 1.53</td><td>$ 2.58</td><td>$ 3.93</td><td>$ 4.58</td></tr>
    <tr><td>144</td><td>$ 1.28</td><td>$ 2.48</td><td>$ 3.02</td><td>$ 3.78</td></tr>
    <tr><td>288</td><td>$ 0.99</td><td>$ 1.63</td><td>$ 2.23</td><td>$ 2.83</td></tr>
    <tr><td>512</td><td>$ 0.69</td><td>$ 1.13</td><td>$ 1.73</td><td>$ 1.98</td></tr></table>
  <div class="section-bar colors-bar">Available Colors:<br>Varsity</div>
  <div class="swatches">
    <div class="swatch" style="background:#0b0b0d">Black</div>
    <div class="swatch" style="background:#9aa3a9">Gray<br>7543C</div>
    <div class="swatch" style="background:#8e2238">Burgundy<br>194C</div>
    <div class="swatch" style="background:#a71f2f">Red<br>187C</div>
    <div class="swatch" style="background:#d0197e">Hot Pink<br>232c</div>
    <div class="swatch" style="background:#f09ab9">Pink<br>1905C</div>
    <div class="swatch" style="background:#3d2660">Purple<br>2685C</div>
    <div class="swatch" style="background:#1e3a6a">Navy<br>654C</div>
    <div class="swatch" style="background:#223d7c">Royal<br>287C</div>
    <div class="swatch" style="background:#149ad5">Columbia<br>299C</div>
    <div class="swatch" style="background:#1ab3e6">Bright Blue<br>306C</div>
    <div class="swatch" style="background:#4a3226">Brown<br>476C</div>
    <div class="swatch" style="background:#17302a">Dark Green<br>5535C</div>
    <div class="swatch" style="background:#0d8a3d">Kelly Green<br>348C</div>
    <div class="swatch" style="background:#8dc63f">Bright<br>Green<br>375C</div>
    <div class="swatch" style="background:#a89549">Vegas<br>Gold<br>4505C</div>
    <div class="swatch" style="background:#c4532a">Texas<br>Orange<br>1525C</div>
    <div class="swatch" style="background:#e8522a">Bright<br>Orange<br>021C</div>
    <div class="swatch" style="background:#f05a28">Orange<br>172C</div>
    <div class="swatch" style="background:#f7a823">Gold<br>1235C</div>
    <div class="swatch" style="background:#fbdd12;color:#333">Yellow<br>YellowC</div>
    <div class="swatch white" style="background:#fff">White</div>
  </div>
  <div class="corner-tab"></div>
</section>

<section class="page cover p3">
  <svg class="wedge" width="523" height="406"><polygon points="0,250 523,95 523,406 0,406" fill="#fff"/></svg>
  <div class="apparel-photo" role="img" aria-label="Cotton sweatshirt and t-shirts with distressed vintage-style printed graphics" style="background:linear-gradient(100deg,#7a1028 0%,#1a1a22 38%,#c8202a 58%,#1c6a3c 80%,#1c5a34 100%)"></div>
  <div class="product-title"><span>CLASSIC</span><br><span>FORMULA</span><br><span>HEAT</span><br><span class="last">TRANSFERS</span></div>
  <div class="fabric-band">
    <h2>FOR COTTON<br>AND<br>COTTON/POLY BLENDS</h2>
    <p>Our Classic ink formula is designed to print on 100% cotton &amp; 50/50 cotton-poly blends. The ink has a very soft feel. Add a distress pattern to your design and give your logo a "classic" time-worn look. Gang sheets allow you to print multiple logos for the same low price! Application is quick and easy! Hot peel them in only 7 seconds!</p>
  </div>
  <div class="color-tag">1, 2, 3 Color</div>
  <div class="corner-tab"></div>
</section>

<section class="page pricing p4">
  <div class="section-bar title-bar">Sizing &amp; Pricing</div>
  <table class="price-table t1"><tr><th>Classic 4x6</th><th>1 color</th><th>2 color</th><th>3 color</th></tr>
    <tr><td>8</td><td>$ 4.83</td><td>$ 8.88</td><td>$ 12.58</td></tr>
    <tr><td>16</td><td>$ 2.43</td><td>$ 4.58</td><td>$ 6.38</td></tr>
    <tr><td>24</td><td>$ 1.63</td><td>$ 3.08</td><td>$ 4.28</td></tr>
    <tr><td>32</td><td>$ 1.28</td><td>$ 2.48</td><td>$ 3.28</td></tr>
    <tr><td>48</td><td>$ 1.13</td><td>$ 2.08</td><td>$ 3.03</td></tr>
    <tr><td>72</td><td>$ 0.88</td><td>$ 1.53</td><td>$ 2.38</td></tr>
    <tr><td>96</td><td>$ 0.68</td><td>$ 1.18</td><td>$ 1.78</td></tr>
    <tr><td>144</td><td>$ 0.48</td><td>$ 1.13</td><td>$ 1.23</td></tr>
    <tr><td>288</td><td>$ 0.38</td><td>$ 0.58</td><td>$ 0.88</td></tr>
    <tr><td>512</td><td>$ 0.23</td><td>$ 0.48</td><td>$ 0.63</td></tr></table>
  <table class="price-table t2"><tr><th>Classic 6x9</th><th>1 color</th><th>2 color</th><th>3 color</th></tr>
    <tr><td>8</td><td>$ 6.28</td><td>$ 11.73</td><td>$ 17.28</td></tr>
    <tr><td>16</td><td>$ 3.18</td><td>$ 5.98</td><td>$ 8.63</td></tr>
    <tr><td>24</td><td>$ 2.18</td><td>$ 4.03</td><td>$ 5.78</td></tr>
    <tr><td>32</td><td>$ 1.73</td><td>$ 3.13</td><td>$ 4.48</td></tr>
    <tr><td>48</td><td>$ 1.53</td><td>$ 2.68</td><td>$ 3.93</td></tr>
    <tr><td>72</td><td>$ 1.28</td><td>$ 2.23</td><td>$ 3.18</td></tr>
    <tr><td>96</td><td>$ 1.08</td><td>$ 1.88</td><td>$ 2.68</td></tr>
    <tr><td>144</td><td>$ 0.98</td><td>$ 1.52</td><td>$ 2.18</td></tr>
    <tr><td>288</td><td>$ 0.68</td><td>$ 1.08</td><td>$ 2.53</td></tr>
    <tr><td>512</td><td>$ 0.48</td><td>$ 0.83</td><td>$ 1.23</td></tr></table>
  <table class="price-table t3"><tr><th>Classic 9x12.75</th><th>1 color</th><th>2 color</th><th>3 color</th></tr>
    <tr><td>8</td><td>$ 6.98</td><td>$ 13.13</td><td>$ 19.13</td></tr>
    <tr><td>16</td><td>$ 3.68</td><td>$ 6.68</td><td>$ 9.58</td></tr>
    <tr><td>24</td><td>$ 2.48</td><td>$ 4.48</td><td>$ 6.43</td></tr>
    <tr><td>32</td><td>$ 2.18</td><td>$ 3.63</td><td>$ 5.13</td></tr>
    <tr><td>48</td><td>$ 1.78</td><td>$ 3.08</td><td>$ 4.33</td></tr>
    <tr><td>72</td><td>$ 1.53</td><td>$ 2.48</td><td>$ 3.58</td></tr>
    <tr><td>96</td><td>$ 1.28</td><td>$ 2.18</td><td>$ 3.13</td></tr>
    <tr><td>144</td><td>$ 1.13</td><td>$ 1.98</td><td>$ 2.58</td></tr>
    <tr><td>288</td><td>$ 0.83</td><td>$ 1.38</td><td>$ 1.88</td></tr>
    <tr><td>512</td><td>$ 0.58</td><td>$ 1.03</td><td>$ 1.48</td></tr></table>
  <table class="price-table t4"><tr><th>Classic 19x12.75</th><th>1 color</th><th>2 color</th><th>3 color</th></tr>
    <tr><td>8</td><td>$ 8.33</td><td>$ 16.13</td><td>$ 23.98</td></tr>
    <tr><td>16</td><td>$ 4.93</td><td>$ 8.93</td><td>$ 13.03</td></tr>
    <tr><td>24</td><td>$ 3.43</td><td>$ 5.98</td><td>$ 8.73</td></tr>
    <tr><td>32</td><td>$ 2.88</td><td>$ 5.13</td><td>$ 7.33</td></tr>
    <tr><td>48</td><td>$ 2.18</td><td>$ 3.73</td><td>$ 5.38</td></tr>
    <tr><td>72</td><td>$ 1.78</td><td>$ 3.23</td><td>$ 4.83</td></tr>
    <tr><td>96</td><td>$ 1.53</td><td>$ 2.58</td><td>$ 3.93</td></tr>
    <tr><td>144</td><td>$ 1.28</td><td>$ 2.48</td><td>$ 3.03</td></tr>
    <tr><td>288</td><td>$ 0.98</td><td>$ 1.63</td><td>$ 2.23</td></tr>
    <tr><td>512</td><td>$ 0.68</td><td>$ 1.13</td><td>$ 1.73</td></tr></table>
  <div class="section-bar colors-bar">Available Colors:<br>Classic</div>
  <div class="swatches">
    <div class="swatch" style="background:#0b0b0d">Black</div>
    <div class="swatch" style="background:#9aa3a9">Gray<br>7543C</div>
    <div class="swatch" style="background:#8e2238">Burgundy<br>194C</div>
    <div class="swatch" style="background:#a71f2f">Red<br>187C</div>
    <div class="swatch" style="background:#d0197e">Hot Pink<br>232c</div>
    <div class="swatch" style="background:#f09ab9">Pink<br>1905C</div>
    <div class="swatch" style="background:#3d2660">Purple<br>2685C</div>
    <div class="swatch" style="background:#1e3a6a">Navy<br>654C</div>
    <div class="swatch" style="background:#223d7c">Royal<br>287C</div>
    <div class="swatch" style="background:#149ad5">Columbia<br>299C</div>
    <div class="swatch" style="background:#1ab3e6">Bright Blue<br>306C</div>
    <div class="swatch" style="background:#4a3226">Brown<br>476C</div>
    <div class="swatch" style="background:#17302a">Dark Green<br>5535C</div>
    <div class="swatch" style="background:#0d8a3d">Kelly Green<br>348C</div>
    <div class="swatch" style="background:#8dc63f">Bright<br>Green<br>375C</div>
    <div class="swatch" style="background:#a89549">Vegas<br>Gold<br>4505C</div>
    <div class="swatch" style="background:#c4532a">Texas<br>Orange<br>1525C</div>
    <div class="swatch" style="background:#e8522a">Bright<br>Orange<br>021C</div>
    <div class="swatch" style="background:#f05a28">Orange<br>172C</div>
    <div class="swatch" style="background:#f7a823">Gold<br>1235C</div>
    <div class="swatch" style="background:#fbdd12;color:#333">Yellow<br>YellowC</div>
    <div class="swatch white" style="background:#fff">White</div>
  </div>
  <div class="corner-tab"></div>
</section>

</body>
</html>
```